Bookcover: Ways to Turn Into a Bold Pathfinder

I am publishing a super-low-cost innovation book for €4,99 on Quillmere Open Press to help everyone become a great innovator: young ambitious people without college education nor a big budget. Do you want to help me?

Brief:
Design a book cover 1600 x 2560 pixels for QOP.
Main title: Ways to Turn Into a Bold Pathfinder
Sub title: mindset - insights - skills & tools
Author: Joost ter Brakel
Design: captive, and appealing to everyone
Target Group: young ambitious people without college education

For quillmere please format the height/width ratio of 1.6:1

```html
<!DOCTYPE html>
<html lang="en">
<head>
<meta charset="utf-8">
<title>Ways to Turn Into a Bold Pathfinder — Joost ter Brakel</title>
<link rel="stylesheet" href="https://fonts.googleapis.com/css2?family=Inter:wght@300;400;700;800&display=swap">
<style>
  :root {
    --paper: #f0ece2;
    --ink: #000000;
    --shade-dark: #3a3a38;
    --shade-light: #e9e6de;
    --accent: #f9bd2e;
  }
  * { margin: 0; padding: 0; box-sizing: border-box; }
  html, body {
    width: 750px;
    height: 1200px;
    overflow: hidden;
    background: var(--paper);
  }
  .cover {
    position: relative;
    width: 750px;
    height: 1200px;
    background: var(--paper);
    font-family: "Inter", Arial, sans-serif;
    color: var(--ink);
  }
  .search-bar {
    position: absolute;
    left: 141px;
    top: 136px;
    width: 497px;
    height: 41px;
    border: 1.5px solid var(--ink);
    border-radius: 21px;
  }
  .search-bar__icon {
    position: absolute;
    left: 10px;
    top: 9px;
    width: 26px;
    height: 26px;
  }
  .search-bar__text {
    position: absolute;
    left: 0;
    right: 0;
    padding-left: 44px;
    top: 7px;
    text-align: center;
    font-size: 23px;
    font-weight: 300;
    letter-spacing: 0.5px;
    line-height: 1;
  }
  .peaks-art {
    position: absolute;
    left: 133px;
    top: 330px;
    width: 457px;
    height: 178px;
    background: linear-gradient(90deg, var(--shade-light) 0%, var(--shade-dark) 45%, var(--shade-light) 100%);
    opacity: 0.55;
  }
  .title {
    position: absolute;
    left: 0;
    width: 750px;
    text-align: center;
    line-height: 1;
    white-space: nowrap;
  }
  .title--light {
    top: 512px;
    font-size: 62px;
    font-weight: 400;
    letter-spacing: -0.5px;
  }
  .title--bold {
    top: 566px;
    font-size: 82px;
    font-weight: 800;
    letter-spacing: -1px;
  }
  .accent-letter { color: var(--accent); }
  .accent-dot {
    display: inline-block;
    width: 0.52em;
    height: 0.52em;
    margin: 0 0.02em;
    border-radius: 50%;
    background: var(--accent);
    vertical-align: baseline;
  }
  .author {
    position: absolute;
    left: 0;
    width: 750px;
    top: 660px;
    text-align: center;
    font-size: 27px;
    font-weight: 400;
    line-height: 1;
  }
  .author-rule {
    position: absolute;
    top: 676px;
    height: 2px;
    background: linear-gradient(90deg, rgba(249,189,46,0), var(--accent) 30%, var(--accent) 70%, rgba(249,189,46,0));
  }
  .author-rule--left { left: 86px; width: 165px; }
  .author-rule--right { left: 483px; width: 183px; }
</style>
</head>
<body>
  <main class="cover">
    <div class="search-bar">
      <svg class="search-bar__icon" viewBox="0 0 26 26" aria-hidden="true">
        <circle cx="11" cy="11" r="9" fill="none" stroke="#000" stroke-width="1.3"/>
        <line x1="17.5" y1="17.5" x2="23" y2="23" stroke="#000" stroke-width="1.5"/>
      </svg>
      <div class="search-bar__text">mindset - insights - skills &amp; tools</div>
    </div>

    <div class="peaks-art" role="img" aria-label="Stylised mountain ridge line illustration with a shaded black-to-white peak"></div>

    <h1>
      <span class="title title--light">Ways t<span class="accent-letter">o</span> Turn Int<span class="accent-letter">o</span> a</span>
      <span class="title title--bold">B<span class="accent-dot"></span>ld Pathfinder</span>
    </h1>

    <div class="author-rule author-rule--left"></div>
    <p class="author">Joost ter Brakel</p>
    <div class="author-rule author-rule--right"></div>
  </main>
</body>
</html>
```